Southern Plantskills Academy needs a modern website that oozes professionalism

Our current website is boring and looks like everyone elses. We need a modern website that says we are the best at plant operator training. We use Brontovex and Hiraketo equipment for our training. We train all over Australia in Civil Construction, Mining and Quarrying. We want to be the "Go to" website for all plant operator training in Australia.

Industry/Entity Type

Heavy Machinery Training

Colors
0054AA
0677BA
7BADD7
CADEEF
E8F1F8
FFF300
FFF600
FEFA6F
FFFEC7
FFFEE8

```html
<!DOCTYPE html>
<html lang="en">
<head>
<meta charset="utf-8">
<title>Southern Plantskills Academy</title>
<link rel="stylesheet" href="https://fonts.googleapis.com/css2?family=Roboto+Condensed:wght@700;800&family=Roboto:wght@400;500&display=swap">
<style>
:root{
  --black:#000;
  --ink:#111;
  --navy:#073a6a;
  --navy-deep:#05305a;
  --yellow:#ffc800;
  --grey:#555;
  --white:#fff;
  --shadow:0 4px 24px rgba(0,0,0,.10);
}
*{box-sizing:border-box;margin:0;padding:0}
html,body{width:1200px;height:3500px;overflow:hidden;background:var(--white)}
body{position:relative;font-family:"Roboto",Arial,sans-serif;color:var(--ink)}
.abs{position:absolute}
.display{font-family:"Roboto Condensed","Arial Narrow",sans-serif;font-weight:800;text-transform:uppercase}

/* header */
.site-header{left:0;top:0;width:1200px;height:75px;background:var(--black)}
.brand{left:111px;top:20px;display:flex;align-items:center;gap:10px;color:var(--white);font-weight:500;font-size:15px}
.brand-dot{width:30px;height:30px;border-radius:50%;background:var(--white)}
.main-nav{left:393px;top:27px;display:flex;gap:26px;color:var(--white);font-size:15px}

/* hero */
.hero{left:0;top:75px;width:1200px;height:488px;background:var(--black)}
.hero-photo{left:560px;top:0;width:640px;height:488px;background:linear-gradient(90deg,#000 0%,#1c2630 25%,#51657a 60%,#6f8094 100%)}
.hero-photo::after{content:"";position:absolute;left:0;right:0;bottom:0;height:140px;background:linear-gradient(180deg,rgba(40,40,40,0),#2b2620)}
.hero-title{left:111px;top:140px;color:var(--white);font-size:64px;line-height:79px;letter-spacing:.5px}
.hero-rule{left:111px;top:388px;width:170px;height:4px;background:var(--yellow)}
.hero-copy{left:111px;top:408px;width:420px;color:var(--white);font-size:18px;line-height:35px}

/* service cards */
.card{top:643px;width:237px;height:336px;background:var(--white);box-shadow:var(--shadow)}
.card-photo{width:237px;height:173px;border-bottom:3px solid var(--yellow)}
.card-body{padding:24px 14px 0 21px}
.card-title{font-size:16.5px;font-weight:700;letter-spacing:0;white-space:nowrap}
.card-text{margin-top:10px;font-size:11px;line-height:22px;color:var(--grey)}
.card-link{display:inline-block;margin-top:4px;font-size:11.5px;font-weight:500;color:var(--navy);text-decoration:underline}

/* giveaway */
.giveaway{left:94px;top:1060px;width:1012px;height:275px;background:var(--black);box-shadow:var(--shadow);overflow:hidden}
.giveaway-photo{left:382px;top:0;width:630px;height:275px;background:linear-gradient(90deg,#000 0%,#3a4a4c 35%,#4d7b86 70%,#8fb3bf 100%)}
.giveaway-title{left:58px;top:30px;color:var(--white);font-size:50px}
.giveaway-sub{left:57px;top:100px;color:var(--white);font-size:28px;line-height:41px;font-weight:700}
.btn{display:flex;align-items:center;justify-content:center;background:var(--yellow);color:var(--ink);font-weight:500;font-size:14.5px;border-radius:0 18px 18px 18px;white-space:nowrap}
.giveaway-btn{left:58px;top:197px;width:128px;height:37px}

/* why choose */
.section-title{color:var(--navy);font-size:47px}
.rule{height:4px;background:var(--yellow)}
.why-title{left:113px;top:1412px}
.why-rule{left:113px;top:1492px;width:170px}
.why-copy{left:113px;top:1524px;width:980px;font-size:15.5px;line-height:31px;color:var(--grey)}

/* features */
.features{left:94px;top:1640px;width:1012px;height:1143px;background:var(--white);box-shadow:var(--shadow)}
.feature-photo{width:450px;height:341px}
.feature-title{color:var(--navy);font-size:26px;font-weight:700}
.feature-rule{width:82px;height:4px;background:var(--yellow)}
.feature-text{font-size:12px;line-height:34px;color:var(--grey)}
.feature-btn{width:118px;height:37px}

/* pay later */
.pay{left:94px;top:2864px;width:1012px;height:275px;background:linear-gradient(90deg,var(--navy-deep),var(--navy) 50%,var(--navy-deep));text-align:center;box-shadow:var(--shadow)}
.pay-title{left:0;top:36px;width:1012px;color:var(--white);font-size:46px}
.pay-sub{left:0;top:98px;width:1012px;color:var(--yellow);font-size:27px}
.pay-copy{left:0;top:150px;width:1012px;color:var(--white);font-size:13.5px}
.pay-btn{left:435px;top:193px;width:143px;height:36px}

/* trusted */
.trusted-title{left:0;top:3210px;width:1200px;text-align:center}
.trusted-rule{left:516px;top:3291px;width:170px}
.trusted-copy{left:150px;top:3318px;width:900px;text-align:center;font-size:15.5px;line-height:31px;color:var(--grey)}

/* footer */
.site-footer{left:0;top:3434px;width:1200px;height:66px;border-top:4px solid var(--yellow);background:var(--white)}
.footer-meta{left:94px;top:26px;display:flex;gap:20px;font-size:12px;color:var(--ink)}
.footer-sep{color:var(--grey)}
.social{left:1022px;top:25px;display:flex;gap:11px}
.social span{width:21px;height:21px;background:var(--navy)}
</style>
</head>
<body>

<header class="site-header abs">
  <div class="brand abs"><span class="brand-dot"></span>Southern Plantskills Academy</div>
  <nav class="main-nav abs">
    <span>About Us</span><span>Courses</span><span>Onsite / Private Courses</span><span>Online Training</span><span>Services</span><span>Student Information</span>
  </nav>
</header>

<section class="hero abs">
  <div class="hero-photo abs" role="img" aria-label="Large yellow mining haul truck on a dirt road at dusk"></div>
  <h1 class="hero-title display abs">Training and<br>experience you<br>can rely on</h1>
  <div class="hero-rule abs"></div>
  <p class="hero-copy abs">Choice and flexibility are on your side. Split your purchases into 4 instalments over 6 weeks.</p>
</section>

<article class="card abs" style="left:94px">
  <div class="card-photo" role="img" aria-label="Trainees in orange hi-vis gathered on a rail worksite" style="background:linear-gradient(180deg,#6f9ccf 0%,#9bb7c9 45%,#a8926b 100%)"></div>
  <div class="card-body"><h3 class="card-title display">Safety Training</h3><p class="card-text">I must explain to you how all this mista ken idea of denouncing pleasure and praising pain was born</p><span class="card-link">Learn More</span></div>
</article>
<article class="card abs" style="left:352px">
  <div class="card-photo" role="img" aria-label="Yellow haul truck in an open-cut mine" style="background:linear-gradient(180deg,#8a8a80 0%,#b59a50 55%,#4b4336 100%)"></div>
  <div class="card-body"><h3 class="card-title display">Coal Mine Training</h3><p class="card-text">I must explain to you how all this mista ken idea of denouncing pleasure and praising pain was born</p><span class="card-link">Learn More</span></div>
</article>
<article class="card abs" style="left:610px">
  <div class="card-photo" role="img" aria-label="Operator in hard hat at an industrial plant control panel" style="background:linear-gradient(135deg,#3c4a4f 0%,#5e7a7a 50%,#a9b83c 100%)"></div>
  <div class="card-body"><h3 class="card-title display">Plant Operator Training</h3><p class="card-text">I must explain to you how all this mista ken idea of denouncing pleasure and praising pain was born</p><span class="card-link">Learn More</span></div>
</article>
<article class="card abs" style="left:868px">
  <div class="card-photo" role="img" aria-label="Two workers in hi-vis vests talking at an industrial site" style="background:linear-gradient(135deg,#7d7f80 0%,#c9cdd0 50%,#d8a640 100%)"></div>
  <div class="card-body"><h3 class="card-title display">High Risk Licences</h3><p class="card-text">I must explain to you how all this mista ken idea of denouncing pleasure and praising pain was born</p><span class="card-link">Learn More</span></div>
</article>

<section class="giveaway abs">
  <div class="giveaway-photo abs" role="img" aria-label="Two people riding a speedboat across the water"></div>
  <h2 class="giveaway-title display abs">Give away</h2>
  <p class="giveaway-sub display abs">Thunderline Cruiser or a boat<br>package worth $35,000</p>
  <span class="btn giveaway-btn abs">Get Started</span>
</section>

<h2 class="section-title display why-title abs">Why choose us?</h2>
<div class="rule why-rule abs"></div>
<p class="why-copy abs">Southern Plantskills Academy consultants have come from the same industries that we consult back to. Our wealth of first hand knowledge and experience enables us to make invaluable contributions to all facets of safety and training in your workplace.</p>

<section class="features abs">
  <div class="feature-photo abs" style="left:506px;top:62px;background:linear-gradient(180deg,#2f7fd8 0%,#6fa6e0 45%,#9c9a8e 70%,#5d5d5d 100%)" role="img" aria-label="Forklift training beside scaffolding in a yard"></div>
  <h3 class="feature-title display abs" style="left:79px;top:118px">We are passionate</h3>
  <div class="feature-rule abs" style="left:79px;top:163px"></div>
  <p class="feature-text abs" style="left:79px;top:180px;width:420px">We are passionate about Health and Safety.<br>I must explain to you how all this mistaken idea of denoun cing plea<br>and praising pain was born and I will give you a complete</p>
  <span class="btn feature-btn abs" style="left:79px;top:303px">Read More</span>

  <div class="feature-photo abs" style="left:56px;top:403px;background:linear-gradient(180deg,#4f86cc 0%,#a9c3df 40%,#4f8a3a 70%,#3d7a2a 100%)" role="img" aria-label="Outdoor training day with a marquee on a lawn"></div>
  <h3 class="feature-title display abs" style="left:549px;top:460px">We are dependable</h3>
  <div class="feature-rule abs" style="left:549px;top:505px"></div>
  <p class="feature-text abs" style="left:549px;top:522px;width:420px">Let us deliver the right training solution for your business.<br>I must explain to you how all this mistaken idea of denoun cing plea<br>and praising pain was born and I will give you a complete</p>
  <span class="btn feature-btn abs" style="left:549px;top:645px">Read More</span>

  <div class="feature-photo abs" style="left:506px;top:744px;background:linear-gradient(180deg,#e9ecee 0%,#cfd3d6 45%,#9a8f5a 70%,#4a4a4c 100%)" role="img" aria-label="Trainees in hi-vis shirts studying at classroom tables"></div>
  <h3 class="feature-title display abs" style="left:79px;top:801px">Nationally recognised</h3>
  <div class="feature-rule abs" style="left:79px;top:846px"></div>
  <p class="feature-text abs" style="left:79px;top:863px;width:420px">We are accredited to delivery nationally recognised training.<br>I must explain to you how all this mistaken idea of denoun cing plea<br>and praising pain was born and I will give you a complete</p>
  <span class="btn feature-btn abs" style="left:79px;top:986px">Read More</span>
</section>

<section class="pay abs" role="img" aria-label="Faded heavy machinery behind a navy overlay">
  <h2 class="pay-title display abs">Buy now, pay later</h2>
  <p class="pay-sub display abs">Buy what you love now. Pay later.</p>
  <p class="pay-copy abs">Choice and flexibility are on your side. Split your purchases into 4 instalments over 6 weeks.</p>
  <span class="btn pay-btn abs">Split My Payment</span>
</section>

<h2 class="section-title display trusted-title abs">Your trusted training partner</h2>
<div class="rule trusted-rule abs"></div>
<p class="trusted-copy abs">We assist our clients in their ongoing quest to achieve zero harm by providing them with the highest calibre of health and safety management advice and personalised training.</p>

<footer class="site-footer abs">
  <div class="footer-meta abs">
    <span>(C) Copyright 2024 | All Rights Reserved</span><span class="footer-sep">|</span>
    <span>RTO Number #40927</span><span class="footer-sep">|</span>
    <span>24 Ridgeway St, Cobalt Creek. Qld 4721</span><span class="footer-sep">|</span>
    <span>1300 555 018</span>
  </div>
  <div class="social abs"><span></span><span></span><span></span></div>
</footer>

</body>
</html>
```